New Business Card Design Project

We require a business card design for Vexalund, a newly established Indian company.
Our focus is on the development, manufacturing, and export of a diverse array of pharmaceutical products on a global scale. The card should convey a professional appearance, as our primary markets are in Africa, China, and Southeast Asian nations.
We envision a two-sided business card, with the reverse side dedicated to a logo set against a solid color or an elegantly designed pattern. The corners should be rounded. We would appreciate seeing both horizontal and vertical design options. We trust the designer to utilize their expertise in creating this design.

The content for the business card is included in the attached Word file.

Target Market(s)

Our primary markets are in Africa, China, and Southeast Asian, Latin America, Maldives, Sri Lanka

Industry/Entity Type

Pharmaceutical Manufacturing and Export

Contact Information for Business Card

Colors

Designer to choose colors to be used in the design.

Requirements
Must have
• The reverse side of the business card features solely the logo along with the tagline, "Care Beyond Borders."
Should not have
• The logo should not exceed two instances, encompassing both the front and back sides of the card.

```html
<!DOCTYPE html>
<html lang="en">
<head>
<meta charset="utf-8">
<title>Vexalund – Business Card</title>
<link rel="stylesheet" href="https://fonts.googleapis.com/css2?family=Poppins:wght@300;400;700&family=Open+Sans:wght@400&display=swap">
<style>
  :root {
    --stage: #232323;
    --card: #212125;
    --edge: #e4513c;
    --blue: #2ea8e0;
    --coral: #f0634e;
    --white: #f2f2f2;
  }
  * { margin: 0; padding: 0; box-sizing: border-box; }
  html, body { width: 1200px; height: 711px; overflow: hidden; }
  body {
    background: var(--stage);
    position: relative;
    font-family: "Open Sans", sans-serif;
  }
  .card {
    position: absolute;
    top: 200px;
    width: 540px;
    height: 310px;
    background: var(--card);
    border-radius: 24px;
    border-bottom: 3px solid var(--edge);
    box-shadow: 0 14px 30px rgba(0,0,0,.55);
    overflow: hidden;
  }
  .card--back { left: 30px; }
  .card--front { left: 630px; }

  /* back side */
  .brand {
    position: absolute;
    left: 0; right: 0; top: 112px;
    display: flex; align-items: center; justify-content: center; gap: 12px;
  }
  .brand__dot {
    width: 22px; height: 22px; border-radius: 50%;
    background: var(--coral);
  }
  .brand__name {
    font-family: "Poppins", sans-serif;
    font-weight: 700;
    font-size: 58px;
    line-height: 1;
    color: var(--blue);
  }
  .tagline {
    position: absolute;
    left: 0; right: 0; top: 196px;
    text-align: center;
    font-family: "Poppins", sans-serif;
    font-weight: 300;
    font-size: 15px;
    letter-spacing: .5px;
    color: var(--white);
  }

  /* front side */
  .front__brand {
    position: absolute;
    right: 70px; top: 42px;
    display: flex; align-items: center; gap: 8px;
  }
  .front__brand .brand__dot { width: 12px; height: 12px; }
  .front__brand .brand__name { font-size: 32px; }
  .accent-bar {
    position: absolute;
    right: 0; top: 96px;
    width: 30px; height: 42px;
    background: var(--coral);
  }
  .person {
    position: absolute;
    right: 40px; top: 96px;
    text-align: right;
  }
  .person__name {
    font-family: "Poppins", sans-serif;
    font-size: 24px;
    line-height: 1.1;
  }
  .person__first { font-weight: 700; color: var(--blue); }
  .person__last { font-weight: 400; color: var(--coral); }
  .person__role {
    font-size: 12px;
    color: var(--white);
    margin-top: 2px;
  }
  .address {
    position: absolute;
    right: 40px; top: 162px;
    text-align: right;
    font-size: 11.5px;
    line-height: 1.45;
    color: var(--blue);
  }
  .contacts {
    position: absolute;
    right: 24px; top: 208px;
    list-style: none;
    text-align: right;
  }
  .contacts li {
    display: flex; justify-content: flex-end; align-items: center; gap: 8px;
    font-size: 12px;
    line-height: 1.9;
    color: var(--white);
  }
  .contacts svg { width: 12px; height: 12px; flex: none; }
</style>
</head>
<body>

  <section class="card card--back" aria-label="Card reverse">
    <div class="brand">
      <span class="brand__dot"></span>
      <span class="brand__name">Vexalund</span>
    </div>
    <p class="tagline">Care Beyond Borders.</p>
  </section>

  <section class="card card--front" aria-label="Card front">
    <div class="front__brand">
      <span class="brand__dot"></span>
      <span class="brand__name">Vexalund</span>
    </div>
    <div class="accent-bar"></div>
    <div class="person">
      <p class="person__name"><span class="person__first">Arjun</span> <span class="person__last">K. Malvade</span></p>
      <p class="person__role">CEO</p>
    </div>
    <p class="address">1840 Lakeshore Rd. Suite 310<br>Nashik, 422011, India</p>
    <ul class="contacts">
      <li>+91 98765 01234
        <svg viewBox="0 0 12 12" aria-hidden="true"><rect x="3" y="0.8" width="6" height="10.4" rx="1" fill="none" stroke="var(--coral)" stroke-width="1.2"/></svg>
      </li>
      <li>www.vexalund.com
        <svg viewBox="0 0 12 12" aria-hidden="true"><circle cx="6" cy="6" r="5" fill="none" stroke="var(--blue)" stroke-width="1.2"/><ellipse cx="6" cy="6" rx="2.2" ry="5" fill="none" stroke="var(--blue)" stroke-width="1"/><line x1="1" y1="6" x2="11" y2="6" stroke="var(--blue)" stroke-width="1"/></svg>
      </li>
      <li>akmalvade@vexalund.com
        <svg viewBox="0 0 12 12" aria-hidden="true"><rect x="0.8" y="2.5" width="10.4" height="7.5" rx="1" fill="none" stroke="var(--coral)" stroke-width="1.2"/><polyline points="1,3 6,7 11,3" fill="none" stroke="var(--coral)" stroke-width="1.2"/></svg>
      </li>
    </ul>
  </section>

</body>
</html>
```